teaching love. a joyful state of being.

adding value to ones circumstance through the teachings of neutralization. quote for back of card: "and then it happens... One day you wake up and you're in this place. You are in this place where everything is right. Your heart is calm. Your soul is lit. Your thoughts are positive. Your vision is clear. Your faith is stronger than ever. And you are at peace. At peace with where you have been. At peace with what you've been through. And at peace with where you're headed." -unknown

Target Market(s)

spiritual, awakening, inspiration, motivation, gratefulness, oneness, peace, positive mindset,

Contact Information for Business Card

front: one line message from quote

Logo Text

up to suggestions

Font styles to use
Serif
Sans Serif
Script

Colors

Designer to choose colors to be used in the design.

Requirements
Must have
• entire quote on one side of card
Nice to have
• simple, and to the point
Should not have
• elaborated designs

```html
<!DOCTYPE html>
<html lang="en">
<head>
<meta charset="utf-8">
<title>Business Card – Front and Back</title>
<link rel="stylesheet" href="https://fonts.googleapis.com/css2?family=Arvo:wght@400;700&family=Tinos:ital@0;1&display=swap">
<style>
  :root {
    --canvas: #e9e9ea;
    --red: #fe0a1a;
    --red-soft: #f7a0a6;
    --brand-pink: #f4b5b5;
    --white: #ffffff;
    --ink: #111111;
    --shadow: rgba(0, 0, 0, 0.18);
  }
  * { box-sizing: border-box; margin: 0; padding: 0; }
  html, body {
    width: 1200px;
    height: 959px;
    overflow: hidden;
    background: var(--canvas);
  }
  .canvas { position: relative; width: 1200px; height: 959px; }
  .card {
    position: absolute;
    width: 620px;
    height: 355px;
    border-radius: 30px;
    overflow: hidden;
    box-shadow: 0 10px 26px var(--shadow);
  }

  /* Back */
  .card--back {
    left: 500px;
    top: 90px;
    background: var(--red);
    display: flex;
    align-items: center;
    justify-content: center;
    padding: 24px 40px;
  }
  .quote {
    font-family: "Arvo", serif;
    color: var(--white);
    font-size: 20px;
    line-height: 1.38;
    text-align: center;
    letter-spacing: 0.4px;
  }
  .quote__source { display: block; text-align: right; padding-right: 120px; }

  /* Front */
  .card--front { left: 80px; top: 500px; background: var(--white); }
  .front-panel { position: absolute; inset: 0; }

  .brand {
    position: absolute;
    left: 40px;
    top: 70px;
    width: 250px;
    text-align: center;
  }
  .brand__mark {
    display: block;
    width: 44px;
    height: 44px;
    margin: 0 auto 12px;
    border-radius: 50%;
    background: var(--brand-pink);
  }
  .brand__name {
    font-family: "Arvo", serif;
    font-weight: 700;
    font-size: 36px;
    line-height: 1.1;
    color: var(--brand-pink);
  }

  .contacts {
    position: absolute;
    left: 34px;
    bottom: 34px;
    list-style: none;
    font-family: "Tinos", serif;
    font-size: 16px;
    color: var(--ink);
    line-height: 1.25;
  }
  .contacts li { display: flex; align-items: center; gap: 10px; }
  .contacts svg { width: 16px; height: 16px; flex: none; }

  .identity {
    position: absolute;
    left: 400px;
    top: 80px;
    font-family: "Arvo", serif;
  }
  .identity__name { color: var(--white); font-size: 25px; font-weight: 400; }
  .identity__role { color: var(--ink); font-size: 28px; font-weight: 700; margin-left: 70px; }

  .tagline {
    position: absolute;
    left: 400px;
    top: 175px;
    width: 200px;
    font-family: "Tinos", serif;
    font-style: italic;
    font-size: 16px;
    line-height: 1.3;
    color: var(--white);
  }

  .address {
    position: absolute;
    left: 408px;
    bottom: 50px;
    display: flex;
    gap: 10px;
    align-items: center;
    font-family: "Tinos", serif;
    font-size: 15px;
    line-height: 1.15;
    color: var(--ink);
  }
  .address svg { width: 16px; height: 20px; flex: none; }
</style>
</head>
<body>
<main class="canvas">

  <section class="card card--back" aria-label="Card back">
    <p class="quote">"and then it happens... One day you wake up and you're in this place. You are in this place where everything is right. Your heart is calm. Your soul is lit. Your thoughts are positive. Your vision is clear. Your faith is stronger than ever. And you are at peace. At peace with where you have been. At peace with what you've been through. And at peace with where you're headed."
      <span class="quote__source">-unknown</span></p>
  </section>

  <section class="card card--front" aria-label="Card front">
    <svg class="front-panel" viewBox="0 0 620 355" preserveAspectRatio="none" aria-hidden="true">
      <path d="M292 0 Q420 150 382 355" fill="none" stroke="var(--red-soft)" stroke-width="14"/>
      <path d="M302 0 Q430 150 392 355 L620 355 L620 0 Z" fill="var(--red)"/>
    </svg>

    <div class="brand">
      <span class="brand__mark"></span>
      <p class="brand__name">Serene<br>Path</p>
    </div>

    <ul class="contacts">
      <li>
        <svg viewBox="0 0 16 16"><rect x="4" y="1" width="8" height="14" rx="1.5" fill="none" stroke="var(--ink)" stroke-width="1.4"/><circle cx="8" cy="12.5" r="0.9" fill="var(--ink)"/></svg>
        +254 700 123 456
      </li>
      <li>
        <svg viewBox="0 0 16 16"><rect x="1" y="3.5" width="14" height="9" fill="none" stroke="var(--ink)" stroke-width="1.4"/><path d="M1 3.5 L8 9 L15 3.5" fill="none" stroke="var(--ink)" stroke-width="1.4"/></svg>
        amaniwanjiru@mailbox.com
      </li>
      <li>
        <svg viewBox="0 0 16 16"><circle cx="8" cy="8" r="6.5" fill="none" stroke="var(--ink)" stroke-width="1.4"/><ellipse cx="8" cy="8" rx="2.8" ry="6.5" fill="none" stroke="var(--ink)" stroke-width="1.2"/><path d="M1.5 8 H14.5" stroke="var(--ink)" stroke-width="1.2"/></svg>
        www.yourdomain.com
      </li>
    </ul>

    <div class="identity">
      <p class="identity__name">Amani Wanjiru</p>
      <p class="identity__role">Manager</p>
    </div>

    <p class="tagline">Your heart is calm. Your soul is lit.</p>

    <div class="address">
      <svg viewBox="0 0 16 20"><path d="M8 19 C3 13 1.5 10 1.5 7.5 A6.5 6.5 0 0 1 14.5 7.5 C14.5 10 13 13 8 19 Z" fill="none" stroke="var(--ink)" stroke-width="1.3"/><circle cx="8" cy="7.5" r="2.2" fill="none" stroke="var(--ink)" stroke-width="1.3"/></svg>
      <p>Street Name, Suit 1234<br>State, Zip Code, Country</p>
    </div>
  </section>

</main>
</body>
</html>
```